Hong Kong based International Remittance and ForEx company requires website design

We need a website designed for a new European - Hong Kong based ForEx & fund remittence entity.

The company specialises in larger corporate & high net worth private client trades, therefore the design must aesthetically reflect this (sophisticated). As a theme colour, financial entities tend to use either blue or red; if blue, our preference is a darker blue. Visually, our preference is less copy, more imagery.

Number of pages would be limited; landing (home), about us, client registration (x1 Corporate form, x1 Private Client form), Contact Us.

Have uploaded the existing logo - please note this is to be redesigned, although the colour scheme will remain the same. Please also note that copy will follow - please use Lorem Ipsum.

Target Market(s)

Medium to large Corporations. High net worth individuals.

Industry/Entity Type

Financial Service

Coding

Coded - Design and coding required

Number of Pages Required

4 page

Font styles to use
Serif

Requirements
Nice to have
• ForEx ticker,

```html
<!DOCTYPE html>
<html lang="en">
<head>
<meta charset="utf-8">
<title>Harbourline Incorporation Limited</title>
<link rel="stylesheet" href="https://fonts.googleapis.com/css2?family=Merriweather:wght@300;400;700&family=Open+Sans:wght@400;600;700&family=Oswald:wght@500&display=swap">
<style>
:root{
  --ink:#2b2b2b;
  --muted:#777;
  --blue:#1a7cc1;
  --blue-dark:#0f5f98;
  --ticker-green:#35d043;
  --ticker-red:#e83030;
  --light:#f3f4f7;
  --skills:#3a3a3a;
  --footer:#242424;
  --footer-bottom:#1b1b1b;
  --rule:#e4e4e4;
  --serif:'Merriweather', Georgia, serif;
  --sans:'Open Sans', Arial, sans-serif;
}
*{box-sizing:border-box;margin:0;padding:0}
html,body{width:1200px;height:2582px;overflow:hidden}
body{background:#fff;font-family:var(--sans);color:var(--ink);position:relative}
.section{position:absolute;left:0;width:1200px}
.abs{position:absolute}

/* ticker */
.ticker{top:0;height:60px;background:linear-gradient(#000,#161616);border-bottom:3px solid var(--blue);
  font-family:'Oswald',sans-serif;font-size:25px;line-height:57px;color:var(--ticker-green);white-space:nowrap;text-align:center;letter-spacing:.5px}
.ticker .down{color:var(--ticker-red)}
.ticker span{margin:0 4px}

/* header */
.site-header{top:60px;height:98px;background:#fff}
.brand{left:86px;top:14px;display:flex;align-items:center;gap:10px}
.brand-mark{width:22px;height:22px;border-radius:50%;background:#c9d3de}
.brand-name{font-family:var(--serif);font-weight:400;font-size:26px;color:#333;line-height:1}
.brand-sub{position:absolute;left:32px;top:34px;font-family:var(--serif);font-weight:400;font-size:8px;letter-spacing:1.5px;color:#333;white-space:nowrap}
.nav a{position:absolute;top:42px;font-family:var(--serif);font-size:12px;color:#555;text-decoration:none;letter-spacing:.3px}
.nav a.active{color:var(--blue)}
.nav .home-dot{position:absolute;left:362px;top:12px;width:24px;height:24px;border-radius:50%;background:#c9d3de}
.icon-btn{position:absolute;top:36px;width:30px;height:30px;border-radius:50%;border:1px solid #ccc;background:#fff}
.flag{position:absolute;left:9px;top:10px;width:10px;height:8px;background:linear-gradient(#2a3f8f 0 33%,#d22 33% 66%,#2a3f8f 66%)}

/* hero */
.hero{top:158px;height:474px;background:
  radial-gradient(ellipse at 75% 40%,rgba(220,60,70,.55),transparent 45%),
  radial-gradient(ellipse at 40% 80%,rgba(120,60,200,.45),transparent 40%),
  radial-gradient(ellipse at 90% 85%,rgba(60,200,120,.35),transparent 35%),
  linear-gradient(120deg,#07101d,#0d2240 55%,#101a2c)}
.hero-title{left:86px;top:148px;color:#fff;font-family:var(--serif)}
.hero-title .t1{display:block;font-weight:300;font-size:34px;letter-spacing:1px;line-height:40px}
.hero-title .t2{display:block;font-weight:700;font-size:45px;letter-spacing:1px;line-height:56px}
.hero-text{left:86px;top:260px;width:420px;color:#fff;font-size:11.5px;line-height:22px;text-transform:uppercase}
.dots{left:90px;top:437px;display:flex;gap:7px}
.dots i{width:12px;height:12px;border-radius:50%;border:2px solid #fff}
.dots i.on{background:#fff}

/* dropdown */
.dropdown{position:absolute;left:439px;top:134px;width:172px;height:188px;background:var(--blue);padding:14px 0 0 14px;z-index:5}
.dropdown li{list-style:none;color:#fff;font-size:11.5px;line-height:35px}
.dropdown li::before{content:"»";margin-right:8px}

/* headings */
.sec-head{width:1200px;text-align:center}
.sec-head .mark{display:inline-block;width:38px;height:38px;border-radius:50%;background:#c9d3de;vertical-align:middle;margin-right:10px}
.sec-head h2{display:inline;font-family:var(--serif);font-weight:400;font-size:20px;color:#333;vertical-align:middle;letter-spacing:.3px}
.sec-sub{width:1200px;text-align:center;font-size:15.5px;color:var(--blue);letter-spacing:.2px}

/* welcome */
.welcome{top:632px;height:530px;background:var(--light)}
.card{top:143px;width:327px;height:340px;background:#fff;border:1px solid #e6e6e6}
.card .photo{height:229px}
.card h3{margin:20px 0 0 14px;font-family:var(--serif);font-weight:400;font-size:12.5px;color:var(--blue);letter-spacing:.5px}
.card p{margin:8px 14px 0;font-size:11px;line-height:22px;color:var(--muted)}

/* about */
.about{top:1162px;height:284px;background:#fff}
.about .frame{left:103px;top:30px;width:212px;height:222px;border:1px solid #ddd;padding:6px;background:#fff}
.about .frame div{width:100%;height:100%;background:linear-gradient(135deg,#e9e4e0,#c89b83 50%,#f2efec)}
.about .head{left:346px;top:40px;display:flex;align-items:center;gap:12px}
.about .head .mark{width:40px;height:40px;border-radius:50%;background:#c9d3de}
.about .head h2{font-family:var(--serif);font-weight:400;font-size:20px;color:#333}
.about .lead{left:346px;top:88px;font-size:15.5px;color:var(--blue)}
.about .body{left:346px;top:120px;width:764px;font-size:11px;line-height:24px;color:#555}
.btn{left:346px;top:205px;width:136px;height:45px;background:var(--blue);color:#fff;font-family:var(--serif);font-weight:700;font-size:12.5px;text-align:center;line-height:45px;letter-spacing:.5px}

/* skills */
.skills{top:1446px;height:370px;background:radial-gradient(ellipse at 70% 40%,#555,#2a2a2a 70%)}
.skills .sec-head h2{color:#fff}
.skills .sec-sub{color:#bbb}
.skill{top:146px;width:180px;text-align:center}
.skill svg{display:block;margin:0 auto}
.skill .pct{position:absolute;left:0;top:40px;width:180px;font-size:24px;color:#fff}
.skill .label{margin-top:22px;font-size:13px;color:#eee;letter-spacing:.5px}

/* blog */
.blog{top:1816px;height:439px;background:#fff}
.post{top:138px;width:248px}
.post .photo{height:193px}
.post h3{margin-top:16px;font-family:var(--serif);font-weight:400;font-size:11.5px;color:#666;letter-spacing:.3px}
.post .meta{margin-top:12px;font-size:11px;color:#888;display:flex;gap:10px;align-items:center}
.post .meta svg{vertical-align:-1px;margin-right:3px}

/* partners */
.partners{top:2255px;height:115px;background:#f1f1f1}
.partner{top:42px;font-family:var(--sans);font-weight:600;font-size:24px;color:#a2a2a2;display:flex;align-items:center;gap:8px}
.partner .sq{width:22px;height:22px;border-radius:50%;background:#b5b5b5}
.arrow{top:45px}

/* footer */
.footer{top:2370px;height:152px;background:var(--footer);color:#fff}
.footer h4{position:absolute;top:30px;font-weight:400;font-size:15px;letter-spacing:.3px}
.footer .lines{position:absolute;top:68px;font-size:11px;line-height:19px;color:#ddd}
.email{left:589px;top:64px;width:210px;height:40px;background:#fff;font-size:11px;color:#888;padding:12px 12px}
.subscribe{left:807px;top:64px;width:92px;height:40px;background:var(--blue);font-weight:700;font-size:11px;text-align:center;line-height:40px}
.social{top:40px;width:34px;height:34px;border-radius:50%;border:2px solid #fff}
.copyright{top:2522px;height:60px;background:var(--footer-bottom);color:#ddd;font-size:11px;text-align:center;line-height:62px;border-top:1px solid #333}
</style>
</head>
<body>

<div class="section ticker">
  <span>▲ 21245 + 1.52</span><span>▲01134 + 2.11</span><span class="down">▼ 05433 – 2.05</span><span>▲ 01112 + 0.57</span><span>▲51231</span><span class="down">▼ 05433 – 2.05</span><span>▲ 01112 + 0.57</span><span>▲51231</span>
</div>

<header class="section site-header">
  <div class="abs brand">
    <span class="brand-mark"></span>
    <span class="brand-name">Harbourline</span>
    <span class="brand-sub">INCORPORATION LIMITED</span>
  </div>
  <nav class="nav">
    <span class="home-dot"></span>
    <a class="active" style="left:353px">HOME</a>
    <a style="left:439px">ABOUT US</a>
    <a style="left:551px">INTERNATIONAL PAYMENTS</a>
    <a style="left:771px">CLIENT APPLICATION</a>
    <a style="left:950px">CONTACT US</a>
  </nav>
  <span class="icon-btn" style="left:1050px;border-color:var(--blue)">
    <svg width="28" height="28" viewBox="0 0 28 28"><circle cx="13" cy="13" r="4" fill="none" stroke="#1a7cc1" stroke-width="1.6"/><line x1="16" y1="16" x2="19" y2="19" stroke="#1a7cc1" stroke-width="1.6"/></svg>
  </span>
  <span class="icon-btn" style="left:1084px"><span class="flag" role="img" aria-label="English language flag"></span></span>
</header>

<ul class="dropdown">
  <li>Making Payments</li>
  <li>Customer Protection</li>
  <li>No Obligation</li>
  <li>Corporate Clients</li>
  <li>Private Clients</li>
</ul>

<section class="section hero" role="img" aria-label="Trading screen with glowing market charts and price lines">
  <div class="abs hero-title"><span class="t1">HARBOURLINE</span><span class="t2">INCORPORATION</span></div>
  <p class="abs hero-text">Harbourline Incorporation Limited is a regulated money service operator number (15-20-04417), licensed authorised by the Hong Kong Customs and Excise.</p>
  <div class="abs dots"><i class="on"></i><i></i><i></i><i></i><i></i></div>
</section>

<section class="section welcome">
  <div class="abs sec-head" style="top:42px"><span class="mark"></span><h2>WELCOME TO OUR COMPANY</h2></div>
  <p class="abs sec-sub" style="top:92px">HARBOURLINE INCORPORATION LIMITED IS A REGULATED MONEY SERVICE OPERATOR</p>

  <article class="abs card" style="left:86px">
    <div class="photo" role="img" aria-label="Business handshake in front of a city skyline at night" style="background:linear-gradient(135deg,#1b2a55,#4a5fa8 55%,#141d3a)"></div>
    <h3>INTERNATIONAL MONEY TRANSFER</h3>
    <p>Harbourline is a leading provider of international payme-<br>exchange to corpo South America...</p>
  </article>
  <article class="abs card" style="left:436px">
    <div class="photo" role="img" aria-label="Colourful foreign exchange chart on a trading display" style="background:linear-gradient(135deg,#3b0f3a,#c43a52 45%,#1f6c8c)"></div>
    <h3>FOREIGN EXCHANGE</h3>
    <p>Harbourline is a leading provider of international payme-<br>exchange to corpo South America...</p>
  </article>
  <article class="abs card" style="left:787px">
    <div class="photo" role="img" aria-label="Stacks of gold coins beside a stock price board" style="background:linear-gradient(135deg,#2a2310,#b98d2a 45%,#1d3a16)"></div>
    <h3>PAYING &amp; RECEIVING AGENCY</h3>
    <p>Harbourline is a leading provider of international payme-<br>exchange to corpo South America...</p>
  </article>
</section>

<section class="section about">
  <div class="abs frame"><div role="img" aria-label="Two hands in a business handshake"></div></div>
  <div class="abs head"><span class="mark"></span><h2>ABOUT US</h2></div>
  <p class="abs lead">HARBOURLINE INCORPORATION LIMITED IS A REGULATED MONEY SERVICE OPERATOR</p>
  <p class="abs body">Harbourline is a leading provider of international payment services and foreign exchange to corporations and individuals covering most of the world including; throughout Asia, South America, and Europe.We engage with our clients with unmatched personalised service and aim to establish longevity with all our client relationships.</p>
  <span class="abs btn">READ MORE</span>
</section>

<section class="section skills" role="img" aria-label="Dimmed photo of hands typing on a keyboard">
  <div class="abs sec-head" style="top:36px"><span class="mark"></span><h2>OUR SKILLS</h2></div>
  <p class="abs sec-sub" style="top:84px">HARBOURLINE INCORPORATION LIMITED IS A REGULATED MONEY SERVICE OPERATOR</p>
  <div class="abs skill" style="left:158px">
    <svg width="120" height="120" viewBox="0 0 120 120"><circle cx="60" cy="60" r="55" fill="none" stroke="#fff" stroke-width="3" stroke-dasharray="328 346" transform="rotate(-90 60 60)"/></svg>
    <span class="pct">95%</span><p class="label">EUROPEAN</p>
  </div>
  <div class="abs skill" style="left:511px">
    <svg width="120" height="120" viewBox="0 0 120 120"><circle cx="60" cy="60" r="55" fill="none" stroke="#fff" stroke-width="3" stroke-dasharray="207 346" transform="rotate(-90 60 60)"/></svg>
    <span class="pct">60%</span><p class="label">HONG KONG</p>
  </div>
  <div class="abs skill" style="left:850px">
    <svg width="120" height="120" viewBox="0 0 120 120"><circle cx="60" cy="60" r="55" fill="none" stroke="#fff" stroke-width="3" stroke-dasharray="173 346" transform="rotate(-90 60 60)"/></svg>
    <span class="pct">50%</span><p class="label">BRITISH</p>
  </div>
</section>

<section class="section blog">
  <div class="abs sec-head" style="top:36px"><span class="mark"></span><h2>LATEST BLOG</h2></div>
  <p class="abs sec-sub" style="top:88px">HARBOURLINE INCORPORATION LIMITED IS A REGULATED MONEY SERVICE OPERATOR</p>

  <article class="abs post" style="left:86px">
    <div class="photo" role="img" aria-label="Calculator and pen on a desk" style="background:linear-gradient(135deg,#eaf2fa,#9fbcd8 60%,#d8e6f2)"></div>
    <h3>DRAWING ON OUR EXPERIENCE</h3>
    <p class="meta"><span><svg width="10" height="10"><rect x="0.5" y="1.5" width="9" height="8" fill="none" stroke="#888"/></svg>May 23, 2016</span><span>○ 4 Comments</span><span>♡ 13</span></p>
  </article>
  <article class="abs post" style="left:346px">
    <div class="photo" role="img" aria-label="Close-up of a payment card chip" style="background:linear-gradient(135deg,#1c2a3a,#6b7d8e 50%,#c7a14a)"></div>
    <h3>DRAWING ON OUR EXPERIENCE</h3>
    <p class="meta"><span><svg width="10" height="10"><rect x="0.5" y="1.5" width="9" height="8" fill="none" stroke="#888"/></svg>May 23, 2016</span><span>○ 4 Comments</span><span>♡ 13</span></p>
  </article>
  <article class="abs post" style="left:606px">
    <div class="photo" role="img" aria-label="Stack of coins on a newspaper" style="background:linear-gradient(135deg,#d9d3c8,#8c8676 55%,#c64a4a)"></div>
    <h3>DRAWING ON OUR EXPERIENCE</h3>
    <p class="meta"><span><svg width="10" height="10"><rect x="0.5" y="1.5" width="9" height="8" fill="none" stroke="#888"/></svg>May 23, 2016</span><span>○ 4 Comments</span><span>♡ 13</span></p>
  </article>
  <article class="abs post" style="left:866px">
    <div class="photo" role="img" aria-label="Business handshake between two people in suits" style="background:linear-gradient(135deg,#f1ede9,#c08a6c 50%,#2b2b2b)"></div>
    <h3>DRAWING ON OUR EXPERIENCE</h3>
    <p class="meta"><span><svg width="10" height="10"><rect x="0.5" y="1.5" width="9" height="8" fill="none" stroke="#888"/></svg>May 23, 2016</span><span>○ 4 Comments</span><span>♡ 13</span></p>
  </article>
</section>

<section class="section partners">
  <svg class="abs arrow" style="left:62px" width="14" height="24" viewBox="0 0 14 24"><polyline points="11,3 3,12 11,21" fill="none" stroke="#999" stroke-width="2"/></svg>
  <div class="abs partner" style="left:103px"><span class="sq"></span>Tunebox</div>
  <div class="abs partner" style="left:271px">Gridsoft</div>
  <div class="abs partner" style="left:455px">Snapline</div>
  <div class="abs partner" style="left:620px">Framestock</div>
  <div class="abs partner" style="left:806px"><span class="sq"></span>Quadra</div>
  <div class="abs partner" style="left:988px">Snapline</div>
  <svg class="abs arrow" style="left:1124px" width="14" height="24" viewBox="0 0 14 24"><polyline points="3,3 11,12 3,21" fill="none" stroke="#999" stroke-width="2"/></svg>
</section>

<footer class="section footer">
  <h4 style="left:98px">CONTACT US</h4>
  <p class="lines" style="left:98px">Harbourline Incorporation Limited<br>126 Lockhart Terrace Central<br>Hong Kong SAR</p>
  <p class="lines" style="left:346px">(852) 2000 4815<br>info@harbourlineincorp.com</p>
  <h4 style="left:589px">NEWSLETTER</h4>
  <div class="abs email">Email:</div>
  <div class="abs subscribe">SUBSCRIBE</div>
  <h4 style="left:990px">FOLLOW US</h4>
  <span class="abs social" style="left:990px;top:64px" aria-label="Social profile"></span>
  <span class="abs social" style="left:1030px;top:64px" aria-label="Social profile"></span>
  <span class="abs social" style="left:1068px;top:64px" aria-label="Social profile"></span>
</footer>

<div class="section copyright">Copyright © 2016 Harbourline Incorporation All rights are reserved</div>

</body>
</html>
```